Fernhale Business Card Design

We are looking for a fresh business card design for our new logo. We would like a business card that is unique but friendly. We are in the window coverings business offering blinds, shutters and shades for homes.

Target Market(s)

Targeting the end-consumer

Industry/Entity Type

Business

Requirements
Must have
• Must have a dedicates space for a photo of our sales person. Must contain our new logo (attached).

```html
<!DOCTYPE html>
<html lang="en">
<head>
<meta charset="utf-8">
<title>Fernhale Business Card</title>
<link href="https://fonts.googleapis.com/css2?family=Roboto:wght@400;500&family=Roboto+Condensed:wght@500&display=swap" rel="stylesheet">
<style>
  :root {
    --backdrop: #2c2c2c;
    --card-white: #f3f3f3;
    --fern-green: #86bf3c;
    --slate-grey: #7c7b80;
    --text-grey: #555555;
    --logo-grey: #7a7a7a;
    --photo-light: #a9a9a9;
    --photo-dark: #8a8a8a;
    --white: #ffffff;
  }
  * { margin: 0; padding: 0; box-sizing: border-box; }
  html, body { width: 1200px; height: 960px; overflow: hidden; }
  body {
    background: var(--backdrop);
    position: relative;
    font-family: "Roboto", Arial, sans-serif;
  }
  .card {
    position: absolute;
    width: 600px;
    height: 342px;
    box-shadow: 0 3px 8px rgba(0,0,0,0.45);
    overflow: hidden;
  }
  /* Front */
  .card-front { left: 314px; top: 113px; background: var(--card-white); }
  .brand { position: absolute; display: flex; align-items: center; }
  .brand-square { background: var(--fern-green); }
  .brand-name { font-family: "Roboto", Arial, sans-serif; font-weight: 400; }
  .card-front .brand { left: 31px; top: 34px; gap: 12px; }
  .card-front .brand-square { width: 44px; height: 44px; }
  .card-front .brand-name { font-size: 36px; color: var(--logo-grey); letter-spacing: 0.2px; }
  .person-name {
    position: absolute; left: 31px; top: 100px;
    font-family: "Roboto Condensed", Arial, sans-serif; font-weight: 500;
    font-size: 21px; color: var(--fern-green); letter-spacing: 0.2px;
  }
  .person-title {
    position: absolute; left: 31px; top: 126px;
    font-size: 14.5px; color: var(--logo-grey);
  }
  .address {
    position: absolute; left: 31px; top: 154px;
    font-size: 14.5px; line-height: 18px; color: var(--text-grey);
  }
  .contacts {
    position: absolute; left: 31px; top: 201px;
    list-style: none; font-size: 14.5px; color: var(--text-grey);
  }
  .contacts li { display: flex; align-items: center; height: 19px; }
  .contacts svg { width: 12px; height: 12px; margin-right: 10px; fill: var(--fern-green); }
  .photo-slot {
    position: absolute; left: 313px; top: 25px; width: 258px; height: 292px;
    background: linear-gradient(180deg, var(--photo-light), var(--photo-dark));
    border-radius: 90px 90px 0 0;
  }
  .front-band { position: absolute; left: 0; bottom: 0; width: 600px; height: 22px; }
  /* Back */
  .card-back { left: 311px; top: 472px; background: var(--fern-green); height: 343px; }
  .card-back .brand { left: 124px; top: 131px; gap: 20px; }
  .card-back .brand-square { width: 76px; height: 76px; background: var(--white); }
  .card-back .brand-name { font-size: 56px; color: var(--white); }
  .back-url {
    position: absolute; left: 0; right: 0; top: 288px; text-align: center;
    font-size: 14px; letter-spacing: 5.5px; color: var(--white);
  }
</style>
</head>
<body>
  <section class="card card-front">
    <div class="brand">
      <span class="brand-square"></span>
      <span class="brand-name">Fernhale</span>
    </div>
    <p class="person-name">DANIEL HART</p>
    <p class="person-title">CEO/FOUNDER</p>
    <p class="address">4120 Maple Ridge Road<br>Juneau, Alaska 34581</p>
    <ul class="contacts">
      <li><svg viewBox="0 0 12 12"><path d="M2.5 0.5 L4.5 0.5 L5.2 3.2 L3.8 4.4 Q5 7 7.6 8.2 L8.8 6.8 L11.5 7.5 L11.5 9.5 Q11.5 11.5 9.5 11.5 Q0.5 10.5 0.5 2.5 Q0.5 0.5 2.5 0.5Z"/></svg>612 480 3917</li>
      <li><svg viewBox="0 0 12 12"><path d="M3 0 H9 V12 H3Z M4 1.5 V9 H8 V1.5Z"/></svg>845 627 1083</li>
      <li><svg viewBox="0 0 12 12"><path d="M3 0 H9 V3 H3Z M0 4 H12 V9 H10 V12 H2 V9 H0Z M3 7 V11 H9 V7Z"/></svg>473 905 2816</li>
      <li><svg viewBox="0 0 12 12"><path d="M0 2 H12 L6 7Z M0 3.5 L6 8.5 L12 3.5 V10 H0Z"/></svg>name@fernhale.com</li>
      <li><svg viewBox="0 0 12 12"><circle cx="6" cy="6" r="6"/></svg>www.fernhale.com</li>
    </ul>
    <div class="photo-slot" role="img" aria-label="Photo of the sales person, arms crossed, wearing a suit and tie"></div>
    <svg class="front-band" viewBox="0 0 600 22" aria-hidden="true">
      <polygon points="0,0 392,0 386,22 0,22" fill="var(--fern-green)"/>
      <polygon points="392,0 396,0 390,22 386,22" fill="var(--white)"/>
      <polygon points="396,0 600,0 600,22 390,22" fill="var(--slate-grey)"/>
    </svg>
  </section>

  <section class="card card-back">
    <div class="brand">
      <span class="brand-square"></span>
      <span class="brand-name">Fernhale</span>
    </div>
    <p class="back-url">www.fernhale.com</p>
  </section>
</body>
</html>
```